Bed Company needs business card

Hello, we are a bed company that makes specialized magnets for beds. We are an alternative healing company. I need a modern and upscale business card. Please incorporate my logo for the card.

Accepted file formats are AI, EPS, and Press-Ready PDFS.

Please include all fonts or convert them to outlines regardless of file type.

If you are designing the card in Photoshop the file Must be 1200dpi.

I am open to anything for the business card.  I really like all of your designs and if you want to change the color of the logo, you can.  I will be making the final selection by Friday.  Thank You for all of your designs.  Feel Free to submit different color logos if you want.  

Reason: I will make a decision Final on Friday April 20th. 2012. Good Luck and Thank you all for the designs.

Target Market(s)

My target Market is people, who are looking for alternative healing.

Industry/Entity Type

Business

Requirements
Must have
• My logo must be incorporated. The front card must have

Name
Job Title

Address
Work
Cell
Fax
email
web

Just put in fake info for the card.

The back of the card. I want the logo on the back with color. I just want it to look modern and cool.

```html
<!DOCTYPE html>
<html lang="en">
<head>
<meta charset="utf-8">
<title>Restfield – Business Card</title>
<link rel="stylesheet" href="https://fonts.googleapis.com/css2?family=Open+Sans:wght@400;600&display=swap">
<style>
  :root {
    --bg: #e6e4e1;
    --card: #ffffff;
    --green-dark: #0f6634;
    --green-light: #52bb4b;
    --ink: #3a3a3a;
    --shadow: rgba(0, 0, 0, 0.28);
  }
  html, body {
    margin: 0;
    padding: 0;
    width: 1200px;
    height: 900px;
    overflow: hidden;
    background: var(--bg);
    font-family: "Open Sans", Arial, sans-serif;
  }
  .canvas {
    position: relative;
    width: 1200px;
    height: 900px;
  }
  .card {
    position: absolute;
    width: 540px;
    height: 310px;
    background: var(--card);
    box-shadow: 4px 6px 14px var(--shadow);
    overflow: hidden;
  }
  .card--front { left: 70px; top: 110px; }
  .card--back  { left: 590px; top: 470px; }

  .front-panel {
    position: absolute;
    left: 0;
    top: 0;
    width: 290px;
    height: 310px;
  }
  .front-details {
    position: absolute;
    left: 308px;
    top: 36px;
    right: 20px;
    color: var(--ink);
  }
  .person-name {
    margin: 0;
    font-size: 27px;
    font-weight: 400;
    line-height: 1.1;
  }
  .person-title {
    margin: 2px 0 0 38px;
    font-size: 15px;
    color: var(--green-dark);
  }
  .contact-list {
    margin: 30px 0 0;
    padding: 0;
    list-style: none;
    font-size: 12.5px;
    line-height: 1.5;
  }
  .contact-list .label {
    display: inline-block;
    width: 30px;
  }
  .contact-list .sep {
    display: inline-block;
    width: 18px;
  }
  .web-block {
    margin-top: 24px;
    font-size: 12.5px;
    line-height: 1.5;
  }
  .web-block .site { color: var(--green-dark); }
  .event-address {
    margin-top: 6px;
    font-size: 9px;
    line-height: 1.5;
  }

  .brand {
    position: absolute;
    left: 78px;
    top: 110px;
    display: flex;
    align-items: center;
    gap: 16px;
  }
  .brand-square {
    width: 44px;
    height: 44px;
    background: var(--green-dark);
  }
  .brand-name {
    font-size: 52px;
    font-weight: 600;
    color: var(--green-light);
    line-height: 1;
  }
  .brand-tagline {
    position: absolute;
    left: 230px;
    top: 178px;
    font-size: 17px;
    letter-spacing: 1.5px;
    color: var(--green-light);
  }
</style>
</head>
<body>
<main class="canvas">
  <section class="card card--front">
    <svg class="front-panel" viewBox="0 0 290 310" role="img" aria-label="Large cross emblem of the brand mark on a green field">
      <rect width="290" height="310" fill="var(--green-dark)"/>
      <rect x="0" y="0" width="290" height="310" fill="none" stroke="var(--green-light)" stroke-width="6"/>
    </svg>
    <div class="front-details">
      <h1 class="person-name">Daniel Reyes</h1>
      <div class="person-title">director</div>
      <ul class="contact-list">
        <li><span class="label">tel</span><span class="sep">:</span>(555) 010 2030</li>
        <li><span class="label">cell</span><span class="sep">:</span>(555) 010 2040</li>
        <li><span class="label">fax</span><span class="sep">:</span>(555) 010 2050</li>
      </ul>
      <div class="web-block">
        <div class="email">office@restfieldsleep.com</div>
        <div class="site">www.restfield-sleep.com</div>
      </div>
      <div class="event-address">May 14-17, 2013, Harbor Hall East,<br>Lakeview IL, Booth 208</div>
    </div>
  </section>

  <section class="card card--back">
    <div class="brand">
      <div class="brand-square"></div>
      <div class="brand-name">Restfield</div>
    </div>
    <div class="brand-tagline">Alternative Healing</div>
  </section>
</main>
</body>
</html>
```